Web landing page design

- Create a Web Design (Uncoded - PSD layout only)

We need a single web page design to promote our service. This page will
acts as a landing page for users and also be utilized in social media
advertising. Please provide us with a cutting edge design. I have attached
a link for what the company is about. In essence we are a photo checking
service which reviews photos for retailers, hotels abd car dealerships to
check everything is good after a service has been performed. Whether it be
a new promotion, cleaning or just checking prices. I am looking for a
design to say that we do many photos and at a very cost effective price
(team based in Mexico)

Link: https://slidevault.example/view/qTr8nWx2LpZk4mHcYdJs/
*Deadline*
5 days
*Updates*

- The Start Here box needs to look like this:

-Start Here (heading)
-A box for email addresses to be entered
-Then a check box with "Yes, I have read and agree to the Privacy Policy
and agree to receive email marketing from Plumora88'
-A submit button

All of this information needs to be in one box please. And please feel
free to contact me if you have any questions about this.

*Target Market(s)*
Retail business, Merchandising companies, Rental property owners, Car
dealers
Updates

Please can you submit entries. I am just looking for a tidy to a presentation already created. Just needs design touches.

Target Market(s)

Ability for audience to understand concept quickly
Benefits to why to use the product stand out
Technology driven approach

Industry/Entity Type

Retail

Number of Pages Required

1 page

Colors
0792cd

Requirements
Must have
• Clean and modern design

```html
<!DOCTYPE html>
<html lang="en">
<head>
<meta charset="utf-8">
<title>Checkora – Transform retail execution</title>
<link rel="stylesheet" href="https://fonts.googleapis.com/css2?family=Lato:wght@400;700;900&family=Open+Sans:wght@400;600&display=swap">
<style>
:root{
  --brand:#0792cd;
  --brand-deep:#1a7fc4;
  --white:#ffffff;
  --ink:#333a40;
  --muted:#555b61;
  --rule:#cfd3d6;
  --frame:rgba(255,255,255,.7);
}
*{box-sizing:border-box;margin:0;padding:0}
html,body{width:1200px;height:937px;overflow:hidden;background:var(--white)}
body{position:relative;font-family:"Open Sans",Arial,sans-serif;color:var(--ink)}
.hero{position:absolute;left:0;top:0;width:1200px;height:722px;overflow:hidden}
.hero-photo{position:absolute;inset:0;
  background:
    linear-gradient(90deg,rgba(70,80,95,.25),rgba(40,60,90,.15) 60%,rgba(40,70,110,.4)),
    radial-gradient(ellipse at 25% 55%,#7a6a55 0%,transparent 45%),
    radial-gradient(ellipse at 70% 55%,#b48a70 0%,transparent 35%),
    radial-gradient(ellipse at 95% 50%,#3f6590 0%,transparent 40%),
    linear-gradient(180deg,#8a8a88 0%,#6d6a62 45%,#6b6257 100%);}
.hero-shade{position:absolute;inset:0;background:rgba(30,30,30,.22)}
.logo{position:absolute;left:98px;top:32px;width:86px;text-align:center;color:var(--white);font-family:"Lato",sans-serif;font-weight:700;font-size:27px}
.logo-mark{display:block;width:38px;height:38px;border-radius:50%;background:var(--brand-deep);margin:0 auto 6px}
.nav{position:absolute;top:56px;left:0;font-family:"Lato",sans-serif;font-weight:700;font-size:17px;color:var(--white)}
.nav a{position:absolute;white-space:nowrap;color:inherit;text-decoration:none}
.nav a.active{color:#2ea6e6}
.search{position:absolute;left:1084px;top:58px}
.headline{position:absolute;left:0;top:142px;width:1200px;text-align:center;color:var(--white);font-family:"Lato",sans-serif;font-weight:700;font-size:48px;line-height:57px;text-shadow:0 2px 6px rgba(0,0,0,.35)}
.start{position:absolute;left:273px;top:282px;width:654px;height:330px;border:2px solid var(--frame);background:rgba(80,80,80,.18)}
.start h2{position:absolute;left:0;top:40px;width:100%;text-align:center;color:var(--white);font-family:"Lato",sans-serif;font-weight:700;font-size:27px}
.email{position:absolute;left:35px;top:92px;width:583px;height:52px;background:var(--white);display:flex;align-items:center;padding-left:19px;font-size:16px;color:#444}
.email svg{margin-right:9px}
.consent{position:absolute;left:35px;top:170px;width:520px;color:var(--white);font-size:14px;line-height:24px}
.consent .box{position:absolute;left:0;top:2px;width:16px;height:16px;border:1.5px solid var(--white);border-radius:2px}
.consent p{padding-left:31px}
.consent p span{display:block;padding-left:4px}
.submit{position:absolute;left:265px;top:244px;width:123px;height:49px;border-radius:25px;background:var(--brand-deep);color:var(--white);font-family:"Lato",sans-serif;font-weight:700;font-size:17px;letter-spacing:.5px;display:flex;align-items:center;justify-content:center}
.dots{position:absolute;left:569px;top:672px;display:flex;gap:4px}
.dots i{width:13px;height:13px;border:1.5px solid var(--white);border-radius:50%}
.dots i.on{background:var(--white)}
.stats{position:absolute;left:0;top:722px;width:1200px;height:119px;border-bottom:1px solid var(--rule)}
.stat{position:absolute;top:0;height:118px;text-align:center}
.stat+.stat{border-left:1px solid var(--rule)}
.stat b{display:block;margin-top:19px;font-family:"Lato",sans-serif;font-weight:700;font-size:45px;line-height:50px;color:var(--brand-deep)}
.stat span{display:block;margin-top:8px;font-size:17px;color:var(--ink)}
.stats .end{position:absolute;left:1101px;top:0;height:118px;border-left:1px solid var(--rule)}
.footer-note{position:absolute;left:100px;top:876px;font-size:13px;color:var(--muted)}
.social{position:absolute;left:979px;top:872px;display:flex;gap:6px}
.social i{width:37px;height:37px;border:1px solid #3a4046;border-radius:50%}
</style>
</head>
<body>
<header class="hero">
  <div class="hero-photo" role="img" aria-label="Blurred retail store background with a person in a denim shirt holding a tablet"></div>
  <div class="hero-shade"></div>
  <div class="logo"><span class="logo-mark"></span>Checkora</div>
  <nav class="nav">
    <a class="active" style="left:634px">Home</a>
    <a style="left:717px">About</a>
    <a style="left:802px">Results</a>
    <a style="left:894px">How</a>
    <a style="left:968px">Free Trials</a>
  </nav>
  <svg class="search" width="18" height="18" viewBox="0 0 18 18" aria-label="Search"><circle cx="7.5" cy="7.5" r="5.5" fill="none" stroke="#fff" stroke-width="2.4"/><line x1="11.5" y1="11.5" x2="16" y2="16" stroke="#fff" stroke-width="2.8" stroke-linecap="round"/></svg>
  <h1 class="headline">Transform retail Execution<br>with a simple photo</h1>
  <section class="start">
    <h2>START HERE</h2>
    <div class="email">
      <svg width="16" height="12" viewBox="0 0 16 12"><rect width="16" height="12" rx="1.5" fill="#333"/><path d="M1 1.5 8 7l7-5.5" fill="none" stroke="#fff" stroke-width="1.4"/></svg>
      Enter Email Address
    </div>
    <div class="consent">
      <span class="box"></span>
      <p>Yes, I have read and agree to the Privacy Policy and agree to receive<span>email marketing from Plumora88</span></p>
    </div>
    <div class="submit">SUBMIT</div>
  </section>
  <div class="dots"><i class="on"></i><i></i><i></i><i></i></div>
</header>
<section class="stats">
  <div class="stat" style="left:0;width:350px;padding-left:40px"><b>2.2M</b><span>Photos reviewed last year</span></div>
  <div class="stat" style="left:350px;width:250px"><b>5P</b><span>From per photo reviewed</span></div>
  <div class="stat" style="left:600px;width:251px"><b>97.2%</b><span>Average compliance</span></div>
  <div class="stat" style="left:851px;width:250px"><b>3-8%</b><span>Sales increase</span></div>
  <div class="end"></div>
</section>
<footer>
  <p class="footer-note">Copyrights © 2018, Checkora. All rights reserved.</p>
  <div class="social" aria-label="Social links"><i></i><i></i><i></i></div>
</footer>
</body>
</html>
```